KRWB new business card design

We need a business card design for our established business which is Australia wide however based in Melbourne. We are a young team of Financial Planners who specialize in Insurance and Basic super advice for people like us.

We are people who help our clients get things done in a timely and cost effective manner whilst having a good time and a laugh along the way.

We would like this to have a consistent feel with our new e-brochure which i have attached from a color and font perspective.

Industry/Entity Type

Business

Requirements
Must have
• We do not need specific address details rather just the states we are in:

VIC/NSW/QLD/TAS
Nice to have
• Curved edge to mate the brochure

```html
<!DOCTYPE html>
<html lang="en">
<head>
<meta charset="utf-8">
<title>KRWB business card set</title>
<link rel="stylesheet" href="https://fonts.googleapis.com/css2?family=Arimo:ital,wght@0,400;0,700;1,400;1,700&family=PT+Sans&display=swap">
<style>
  :root {
    --backdrop: #8b5d3a;
    --card-white: #ffffff;
    --card-black: #161616;
    --green-deep: #0fa552;
    --green-light: #6cbf4f;
    --green-bright: #7ac943;
    --ink: #2b2b2b;
    --ink-soft: #6d6d6d;
    --ink-grey: #3c3c3c;
    --label: #111111;
  }
  * { box-sizing: border-box; margin: 0; padding: 0; }
  html, body { width: 1200px; height: 788px; overflow: hidden; }
  body {
    position: relative;
    background: var(--backdrop);
    font-family: "Arimo", Arial, sans-serif;
    color: var(--ink);
  }
  .view-label {
    position: absolute;
    font-family: "PT Sans", Arial, sans-serif;
    font-size: 22px;
    color: var(--label);
    transform: translateX(-50%);
  }
  .card {
    position: absolute;
    width: 525px;
    height: 300px;
    border-radius: 18px;
    background: var(--card-white);
    overflow: hidden;
    box-shadow: 0 4px 10px rgba(0,0,0,.35);
  }
  .card--dark { background: var(--card-black); }
  .card > * { position: absolute; }

  /* brand name block */
  .brand { display: flex; flex-direction: column; align-items: flex-start; }
  .brand__square { width: 56px; height: 56px; background: var(--green-light); margin-bottom: 14px; }
  .brand__name { font-weight: 700; font-size: 30px; line-height: 1.05; color: var(--ink); white-space: nowrap; }
  .brand--compact .brand__name { font-size: 24px; }
  .brand--large .brand__square { width: 70px; height: 70px; }
  .brand--large .brand__name { font-size: 32px; color: #ffffff; }

  /* front */
  .holder { left: 315px; top: 30px; }
  .holder__name { font-size: 19px; font-weight: 700; color: var(--ink-grey); }
  .holder__creds { font-size: 13.5px; font-weight: 700; color: var(--ink-grey); line-height: 1.5; margin-top: 3px; }
  .contacts { left: 315px; top: 120px; font-size: 14px; color: var(--ink-grey); line-height: 26px; }
  .contacts b { font-style: italic; }
  .footer-band { left: 0; bottom: 0; width: 525px; height: 52px; }
  .online { left: 315px; bottom: 11px; color: #fff; font-size: 14px; line-height: 18px; }
  .online b { font-style: italic; }

  /* backs */
  .divider { left: 260px; top: 20px; width: 2px; height: 238px; background: linear-gradient(#fff, #777 50%, #fff); }
  .services { list-style: none; }
  .services .services__title { font-size: 18px; font-style: italic; line-height: 22px; margin-bottom: 13px; }
  .services .services__title::before { content: none; }
  .services li { font-size: 14px; font-weight: 700; line-height: 34px; }
  .services li::before { content: "\25AA\00a0"; }
  .services--grey { color: var(--ink-soft); }
  .services--center { text-align: center; color: var(--ink-grey); }
  .services--white { color: #fff; }
  .tagline-band {
    left: 0; bottom: 0; width: 100%; height: 39px;
    background: var(--green-light); color: #fff;
    font-size: 14px; font-weight: 700;
    display: flex; align-items: center; justify-content: center;
  }
  .tagline { font-size: 14px; font-weight: 700; }
  .tagline--centered { left: 0; width: 525px; text-align: center; bottom: 17px; color: var(--ink-grey); }
  .tagline--green { left: 313px; top: 253px; color: var(--green-bright); line-height: 18px; }
</style>
</head>
<body>
  <span class="view-label" style="left:320px;top:32px">Front</span>
  <span class="view-label" style="left:895px;top:32px">Back - 1</span>
  <span class="view-label" style="left:310px;top:403px">Back - 2</span>
  <span class="view-label" style="left:895px;top:403px">Back - 3</span>

  <!-- Front -->
  <section class="card" style="left:53px;top:72px">
    <div class="brand" style="left:58px;top:60px">
      <span class="brand__square"></span>
      <span class="brand__name">Kestrel Ridge<br>Wealth</span>
    </div>
    <div class="holder">
      <p class="holder__name">Daniel Marsh</p>
      <p class="holder__creds">ADFS, BBus, LRS©<br>Financial Adviser</p>
    </div>
    <p class="contacts">
      <b>cell</b> 0400 555 218<br>
      <b>phone</b> 1300 555 742<br>
      <b>fax</b> 03 9555 0184<br>
      VIC/NSW/QLD/TAS
    </p>
    <svg class="footer-band" viewBox="0 0 525 52" aria-hidden="true">
      <polygon points="290,0 525,0 525,52 250,52" fill="var(--green-deep)"/>
      <polygon points="0,22 265,22 248,40 0,40" fill="var(--green-deep)"/>
      <polygon points="0,40 248,40 236,52 0,52" fill="var(--green-light)"/>
    </svg>
    <p class="online"><b>email</b> daniel@krwb.com.au<br><b>web</b> www.krwb.com.au</p>
  </section>

  <!-- Back 1 -->
  <section class="card" style="left:622px;top:74px">
    <div class="brand brand--compact" style="left:76px;top:60px">
      <span class="brand__square"></span>
      <span class="brand__name">Kestrel Ridge<br>Wealth</span>
    </div>
    <span class="divider"></span>
    <ul class="services services--grey" style="left:320px;top:45px">
      <li class="services__title">Specialising in</li>
      <li>Risk Insurance</li>
      <li>Debt Management</li>
      <li>Superannuation</li>
      <li>Wealth Creation</li>
      <li>Retirement Planning</li>
    </ul>
    <p class="tagline-band">SECURE FUTURE, ENHANCED LIFESTYLE</p>
  </section>

  <!-- Back 2 -->
  <section class="card" style="left:53px;top:446px">
    <ul class="services services--center" style="left:0;width:525px;top:45px">
      <li class="services__title">Specialising in</li>
      <li>Risk Insurance</li>
      <li>Debt Management</li>
      <li>Superannuation</li>
      <li>Wealth Creation</li>
      <li>Retirement Planning</li>
    </ul>
    <p class="tagline tagline--centered">SECURE FUTURE, ENHANCED LIFESTYLE</p>
  </section>

  <!-- Back 3 -->
  <section class="card card--dark" style="left:622px;top:446px">
    <div class="brand brand--large" style="left:64px;top:64px">
      <span class="brand__square"></span>
      <span class="brand__name">Kestrel Ridge<br>Wealth</span>
    </div>
    <ul class="services services--white" style="left:314px;top:22px">
      <li class="services__title">Specialising in</li>
      <li>Risk Insurance</li>
      <li>Debt Management</li>
      <li>Superannuation</li>
      <li>Wealth Creation</li>
      <li>Retirement Planning</li>
    </ul>
    <p class="tagline tagline--green">SECURE FUTURE<br>ENHANCED LIFESTYLE</p>
  </section>
</body>
</html>
```